Thornbury Building Company - Card Design

I am looking to use the logo designs that you already did for me to develop a business card. I would like the card to have a black background and be double sided. I want white and green logo and text. I have attached an inspiration photo of a look that I like. I would like to use the Vertical Logo attached to take up the full front side of the card. On the back where I have my name and information, I would like to have the horizontal logo or maybe even just the image of the 'A' and trees without the text. I am open, but I am looking for something clean and simple and I want the green to really pop! Additional files can be found under Design #: 58302946

Target Market(s)

Homeowners

Industry/Entity Type

Construction

Contact Information for Business Card

Name: Marcus Thornbury, Title: Project Manager, Phone: 555.274.8136, Email: thornburybuildingcompany@mailvesta.com, address: 487 Larkspur Ln, Cedarwick, WS 95033, Lic# 2468317

Colors
00AB8E
00BBA5
67D7C9
C6EFE9
E9F9F6

Requirements
Nice to have
• I would like to see the logos that I have already got from ArtLoomHub, though I am open to new ones

```html
<!DOCTYPE html>
<html lang="en">
<head>
<meta charset="utf-8">
<title>Thornbury Building Company – Business Card</title>
<link href="https://fonts.googleapis.com/css2?family=Montserrat:wght@400;500;600;700&display=swap" rel="stylesheet">
<style>
  :root {
    --backdrop: #8a7558;
    --card: #222222;
    --green: #6abf4b;
    --white: #ffffff;
    --shadow: rgba(0, 0, 0, 0.45);
  }
  * { margin: 0; padding: 0; box-sizing: border-box; }
  html, body {
    width: 900px;
    height: 1200px;
    overflow: hidden;
  }
  body {
    position: relative;
    background: var(--backdrop);
    font-family: "Montserrat", sans-serif;
    color: var(--white);
  }
  .card {
    position: absolute;
    left: 80px;
    width: 742px;
    height: 442px;
    background: var(--card);
    border-radius: 40px;
    box-shadow: 0 4px 8px var(--shadow);
    overflow: hidden;
  }
  .card--front { top: 130px; }
  .card--back { top: 638px; }

  .brand {
    position: absolute;
    display: flex;
    align-items: center;
    font-weight: 600;
    color: var(--white);
    text-transform: uppercase;
    letter-spacing: 0.06em;
  }
  .brand__square {
    background: var(--green);
    flex: none;
  }
  .brand__name { line-height: 1.15; }

  .card--front .brand {
    left: 0;
    width: 343px;
    top: 170px;
    flex-direction: column;
    text-align: center;
    gap: 14px;
    font-size: 22px;
  }
  .card--front .brand__square { width: 48px; height: 48px; }

  .card--back .brand {
    left: 0;
    right: 0;
    top: 170px;
    justify-content: center;
    gap: 26px;
    font-size: 40px;
  }
  .card--back .brand__square { width: 96px; height: 96px; }

  .divider {
    position: absolute;
    left: 342px;
    top: 150px;
    width: 2px;
    height: 193px;
    background: var(--green);
  }

  .contact {
    position: absolute;
    left: 378px;
    top: 152px;
  }
  .contact__name {
    font-size: 27px;
    font-weight: 700;
    color: var(--green);
    line-height: 1.1;
  }
  .contact__title {
    font-size: 16px;
    font-weight: 400;
    margin-top: 3px;
  }
  .contact__license {
    font-size: 16px;
    font-weight: 600;
    margin-top: 20px;
  }
  .contact__license-label { color: var(--green); font-weight: 500; }
  .contact__list {
    list-style: none;
    margin-top: 14px;
  }
  .contact__item {
    display: flex;
    align-items: center;
    gap: 11px;
    font-size: 16px;
    height: 26px;
  }
  .contact__item--email { font-size: 15px; }
  .contact__icon {
    width: 15px;
    height: 15px;
    fill: var(--green);
    flex: none;
  }
</style>
</head>
<body>

<section class="card card--front" aria-label="Business card front">
  <div class="brand">
    <span class="brand__square"></span>
    <span class="brand__name">Thornbury<br>Building Company</span>
  </div>

  <div class="divider"></div>

  <div class="contact">
    <h1 class="contact__name">Marcus Thornbury</h1>
    <p class="contact__title">Project Manager</p>
    <p class="contact__license"><span class="contact__license-label">Lic</span> #2468317</p>
    <ul class="contact__list">
      <li class="contact__item">
        <svg class="contact__icon" viewBox="0 0 16 16" aria-hidden="true"><path d="M8 0a5.5 5.5 0 0 0-5.5 5.5C2.5 10 8 16 8 16s5.5-6 5.5-10.5A5.5 5.5 0 0 0 8 0zm0 7.8a2.3 2.3 0 1 1 0-4.6 2.3 2.3 0 0 1 0 4.6z"/></svg>
        487 Larkspur Ln, Cedarwick, WS 95033
      </li>
      <li class="contact__item">
        <svg class="contact__icon" viewBox="0 0 16 16" aria-hidden="true"><path d="M1 5c0-2 3-3 7-3s7 1 7 3v1.5h-3.5V5h-7v1.5H1zM3 8h10l1.5 6h-13zm5 1.5a2 2 0 1 0 0 4 2 2 0 0 0 0-4z"/></svg>
        555.274.8136
      </li>
      <li class="contact__item contact__item--email">
        <svg class="contact__icon" viewBox="0 0 16 16" aria-hidden="true"><path d="M1 3h14v1.2L8 9 1 4.2zm0 2.8 7 4.8 7-4.8V13H1z"/></svg>
        thornburybuildingcompany@mailvesta.com
      </li>
    </ul>
  </div>
</section>

<section class="card card--back" aria-label="Business card back">
  <div class="brand">
    <span class="brand__square"></span>
    <span class="brand__name">Thornbury<br>Building Company</span>
  </div>
</section>

</body>
</html>
```